Business Card Design needed - Something Awesome!

Need a business card designed. Company is "Marlowe Advisory" we do consulting and also have sales automation technology.
I'm going to use thick stock or metal, something really nice... I was thinking about a QR Code on the back that would just upload my contact info to the persons contact, etc -

This is a Strategy Company with a tech feel. I'm open to ideas but really want this to be nice!

I need a template that should include:

Name | Position or Title
D: 415.902.3376
www.marloweadvisory.example

I'm going to attach my contact so you can use that one, I need to get this printed.

Target Market(s)

Small to mid size customers, Entrepreneurs etc.

Industry/Entity Type

Consulting, Tech, Private Equity.

Contact Information for Business Card

Name, Phone, Maybe email, URL

Font styles to use
Sans Serif

Colors

Designer to choose only greyscale colors for use in the design.

Requirements
Must have
• Fresh, Clean, stand out from the crowd - will be on thick stock or metal.
Nice to have
• Clean, simple yet impactful.
Should not have
• Not cartoonish

```html
<!DOCTYPE html>
<html lang="en">
<head>
<meta charset="utf-8">
<title>Marlowe Advisory — Business Card</title>
<link href="https://fonts.googleapis.com/css2?family=Roboto:wght@300;400;500;700&display=swap" rel="stylesheet">
<style>
  :root {
    --backdrop: #3b3b3c;
    --card: #141414;
    --card-edge: #0a0a0a;
    --silver: #c9c9c9;
    --silver-soft: #9a9a9a;
    --rule: #6d6d6d;
    --pattern-dark: #0c0c0c;
    --pattern-mid: #2a2a2a;
  }
  * { box-sizing: border-box; margin: 0; padding: 0; }
  html, body {
    width: 1200px; height: 801px; overflow: hidden;
    background: var(--backdrop);
    font-family: "Roboto", Arial, sans-serif;
  }
  .stage {
    position: relative; width: 1200px; height: 801px;
    display: flex; align-items: center; justify-content: center; gap: 56px;
  }
  .card {
    position: relative; width: 520px; height: 298px;
    background: var(--card);
    border: 1px solid var(--card-edge);
    box-shadow: 0 14px 30px rgba(0,0,0,.35);
    overflow: hidden;
  }
  .wordmark {
    font-weight: 400; color: var(--silver);
    letter-spacing: 3px; text-transform: uppercase; white-space: nowrap;
  }

  /* Front: contact side */
  .card-front .wordmark {
    position: absolute; left: 34px; top: 124px; font-size: 30px;
  }
  .identity {
    position: absolute; right: 30px; top: 30px; text-align: right;
  }
  .identity-name {
    font-weight: 700; font-size: 17px; letter-spacing: 1px;
    color: var(--silver); text-transform: uppercase;
  }
  .identity-title {
    margin-top: 4px; font-size: 12px; font-weight: 400; color: var(--silver-soft);
  }
  .rule-top {
    position: absolute; right: 30px; top: 82px; width: 270px; height: 1px;
    background: var(--rule);
  }
  .rule-bottom {
    position: absolute; left: 30px; bottom: 96px; width: 270px; height: 1px;
    background: var(--rule);
  }
  .contact-list {
    position: absolute; left: 30px; bottom: 24px; list-style: none;
  }
  .contact-list li {
    display: flex; align-items: center; gap: 8px;
    font-size: 13px; font-weight: 300; color: var(--silver);
    line-height: 21px;
  }
  .contact-list svg { width: 11px; height: 11px; fill: var(--silver); flex: none; }

  /* Back: brand side */
  .card-back .pattern {
    position: absolute; inset: 0;
    background: linear-gradient(125deg, var(--pattern-dark) 0%, #181818 45%, var(--pattern-mid) 100%);
  }
  .card-back .wordmark {
    position: absolute; left: 50%; top: 50%;
    transform: translate(-50%, -50%); font-size: 34px;
  }
</style>
</head>
<body>
  <main class="stage">
    <article class="card card-front">
      <div class="wordmark">Marlowe Advisory</div>
      <div class="identity">
        <div class="identity-name">Corin T. Halvorsen</div>
        <div class="identity-title">Founder / CEO</div>
      </div>
      <div class="rule-top"></div>
      <div class="rule-bottom"></div>
      <ul class="contact-list">
        <li>
          <svg viewBox="0 0 24 24" aria-hidden="true"><path d="M6.6 10.8a15.1 15.1 0 0 0 6.6 6.6l2.2-2.2a1 1 0 0 1 1-.25 11.4 11.4 0 0 0 3.6.57 1 1 0 0 1 1 1V20a1 1 0 0 1-1 1A17 17 0 0 1 3 4a1 1 0 0 1 1-1h3.5a1 1 0 0 1 1 1c0 1.25.2 2.45.57 3.57a1 1 0 0 1-.25 1z"/></svg>
          415.902.3376
        </li>
        <li>
          <svg viewBox="0 0 24 24" aria-hidden="true"><path d="M2 5h20v14H2zm2 2v.5l8 5 8-5V7z"/></svg>
          info@marloweadvisory.example
        </li>
        <li>
          <svg viewBox="0 0 24 24" aria-hidden="true"><path d="M12 2a10 10 0 1 0 0 20 10 10 0 0 0 0-20zm6.9 9h-3a15 15 0 0 0-1.3-5.6A8 8 0 0 1 18.9 11zM12 4c.9 1.2 1.8 3.6 1.9 7h-3.8C10.2 7.6 11.1 5.2 12 4zM9.4 5.4A15 15 0 0 0 8.1 11h-3a8 8 0 0 1 4.3-5.6zM5.1 13h3a15 15 0 0 0 1.3 5.6A8 8 0 0 1 5.1 13zM12 20c-.9-1.2-1.8-3.6-1.9-7h3.8c-.1 3.4-1 5.8-1.9 7zm2.6-1.4a15 15 0 0 0 1.3-5.6h3a8 8 0 0 1-4.3 5.6z"/></svg>
          www.marloweadvisory.example
        </li>
      </ul>
    </article>

    <article class="card card-back">
      <div class="pattern" role="img" aria-label="Glossy spot-varnish pattern of staggered dark squares across the card"></div>
      <div class="wordmark">Marlowe Advisory</div>
    </article>
  </main>
</body>
</html>
```